Construction business card

I need a new business card, they can connect with my logo, brand.
What we do is residential house , design and build
I like: Navy blue / black
I attached our logo, brand,
and, some idea for business card.

```html
<!DOCTYPE html>
<html lang="en">
<head>
<meta charset="utf-8">
<title>Arden Building Group – Business Card</title>
<link href="https://fonts.googleapis.com/css2?family=Arimo:wght@400;700&display=swap" rel="stylesheet">
<style>
  :root {
    --backdrop: #1f1f21;
    --card-blue: #3a88c9;
    --card-ink: #ffffff;
    --mark-dark: #1b1e23;
    --shadow: rgba(0,0,0,0.55);
  }
  * { box-sizing: border-box; margin: 0; padding: 0; }
  html, body {
    width: 1200px; height: 801px; overflow: hidden;
    background: var(--backdrop);
    font-family: "Arimo", Arial, sans-serif;
  }
  .sheet {
    position: relative; width: 1200px; height: 801px;
    display: flex; align-items: center; justify-content: center; gap: 50px;
  }
  .card {
    position: relative;
    width: 520px; height: 300px;
    background: var(--card-blue);
    border-radius: 22px;
    box-shadow: 0 14px 34px var(--shadow);
    color: var(--card-ink);
    overflow: hidden;
  }
  /* front */
  .front-mark {
    position: absolute; right: 28px; top: 22px;
    font-weight: 700; font-size: 62px; letter-spacing: 2px;
    color: var(--mark-dark); line-height: 1;
  }
  .contact {
    position: absolute; left: 34px; bottom: 24px;
    font-size: 12.5px; line-height: 1.45;
  }
  .contact .person-name { font-weight: 700; font-size: 20px; letter-spacing: .5px; line-height: 1.1; }
  .contact .person-role { font-size: 13.5px; }
  .contact .rule { width: 12px; height: 1px; background: var(--card-ink); margin: 7px 0; }
  .contact .line { display: flex; align-items: center; gap: 7px; }
  .contact svg { width: 11px; height: 11px; flex: none; }
  /* back */
  .back-name {
    position: absolute; inset: 0;
    display: flex; align-items: center; justify-content: center; gap: 14px;
    font-weight: 700; font-size: 32px; letter-spacing: 1px; text-transform: uppercase;
  }
  .back-name .badge { width: 16px; height: 16px; background: var(--card-ink); flex: none; }
</style>
</head>
<body>
<main class="sheet">
  <section class="card card-front">
    <div class="front-mark">ARDEN</div>
    <div class="contact">
      <p class="person-name">DANA WHITLOW</p>
      <p class="person-role">CEO/Founder</p>
      <div class="rule"></div>
      <p>28 Fernhill Rd,</p>
      <p>Ashgrove, VIC 3150</p>
      <div class="rule"></div>
      <p class="line">
        <svg viewBox="0 0 12 12" aria-hidden="true"><path d="M3 1l2 2.5-1.2 1.2c.7 1.4 1.8 2.5 3.2 3.2L8.2 6.7 10.8 8.8 9.6 11C5 10.6 1.4 7 1 2.4z" fill="#fff"/></svg>
        0400 555 018
      </p>
      <p class="line">
        <svg viewBox="0 0 12 12" aria-hidden="true"><rect x="1" y="2.5" width="10" height="7" fill="none" stroke="#fff" stroke-width="1.2"/><path d="M1 3l5 3.5L11 3" fill="none" stroke="#fff" stroke-width="1.2"/></svg>
        info@ardenbuildinggroup.com.au
      </p>
      <p class="line">
        <svg viewBox="0 0 12 12" aria-hidden="true"><circle cx="6" cy="6" r="4.8" fill="none" stroke="#fff" stroke-width="1.2"/><ellipse cx="6" cy="6" rx="2" ry="4.8" fill="none" stroke="#fff" stroke-width="1"/><path d="M1.2 6h9.6" stroke="#fff" stroke-width="1"/></svg>
        ardenbuildinggroup.com.au
      </p>
    </div>
  </section>
  <section class="card card-back">
    <div class="back-name"><span class="badge"></span>Arden Building Group</div>
  </section>
</main>
</body>
</html>
```